Fun Employee News and Engagement Portal - Tidy Hearth Company

We are looking for a clean, but fun WordPress template for an internal employee engagement website. The site will be a place we share news, fun stories and pictures. We'll provide space for our employees to post comments, etc.
We are a deep dish pizza restaurant with a rich history. I'd love to see your take on a look and feel for us! The site will be called Bim-Zee. I've posted some images and colors along with this brief description.
Focus on making the template whimsical and fun! (Extra point for focusing on the "Lettering in lights" ).
I will continue to post additional pieces of art and content examples.
Reason: Our team is continuing to review designs. We've decided to extend the timing a few more days. Good luck! Make it playful!
Reason: We need more time with our team to review these designs. We are going to extend one more time!
Reason: Still trying to get enough time to review with the Bim-Zee team!
Reason: We are continuing to evaluate designs. Thank you!
Industry/Entity Type
American Restaurant
Number of Pages Required
1 page
Look and feel
Each slider illustrates characteristics of the customer's brand and the style your logo design should communicate.

```html
<!DOCTYPE html>
<html lang="en">
<head>
<meta charset="utf-8">
<title>Bim-Zee — Tidy Hearth Company</title>
<link href="https://fonts.googleapis.com/css2?family=Roboto+Slab:wght@400;700;800&family=Open+Sans:wght@400;600;700&display=swap" rel="stylesheet">
<style>
:root{
  --red:#e0102a;
  --red-dark:#b80c21;
  --ink:#222;
  --text:#666;
  --muted:#999;
  --line:#e2e2e2;
  --band:#e9e9e9;
  --white:#fff;
  --crust:#c98a3c;
  --sauce:#a8301c;
  --wood:#5a3a22;
}
*{box-sizing:border-box;margin:0;padding:0}
html,body{width:1200px;height:4044px;overflow:hidden}
body{font-family:"Open Sans",Arial,sans-serif;color:var(--text);background:var(--white);font-size:13px;line-height:1.6}
.wrap{width:936px;margin:0 auto;position:relative}
.photo{display:block}
.btn-outline{display:inline-block;border:1px solid var(--red);color:var(--red);font-size:9px;font-weight:700;letter-spacing:.5px;text-transform:uppercase;padding:5px 10px;line-height:1}
.btn-red{display:inline-block;background:var(--red);color:var(--white);font-size:9px;font-weight:700;letter-spacing:.5px;text-transform:uppercase;padding:6px 12px;line-height:1}
.section-title{font-family:"Roboto Slab",Georgia,serif;font-weight:700;font-size:24px;color:var(--red);text-transform:uppercase;line-height:1}

/* hero */
.hero{height:660px;position:relative;background:radial-gradient(ellipse 480px 420px at 600px 260px,#b3431f 0%,#8e2f18 45%,#4a2a18 75%,#2e1d12 100%);overflow:hidden}
.hero-shade{position:absolute;inset:0;background:linear-gradient(rgba(0,0,0,.25),rgba(0,0,0,.15))}
.site-header{position:absolute;top:0;left:0;right:0;height:44px;z-index:2}
.site-header .wrap{display:flex;align-items:center;height:44px}
.logo{font-family:"Roboto Slab",Georgia,serif;font-weight:800;font-size:30px;color:var(--red);line-height:1}
.site-header .logo{font-size:26px;background:var(--white);padding:4px 10px}
.main-nav{display:flex;margin-left:auto;margin-right:300px}
.main-nav a{color:var(--white);font-size:9px;font-weight:700;text-transform:uppercase;padding:16px 14px;line-height:1}
.main-nav a.active{background:var(--red)}
.search{position:absolute;right:0;top:12px;width:100px;height:20px;background:var(--white);border-radius:2px;font-size:9px;color:var(--muted);padding:3px 8px}
.hero-copy{position:absolute;top:282px;left:0;right:0;text-align:center;z-index:2}
.hero-copy h1{font-family:"Roboto Slab",Georgia,serif;font-weight:700;font-size:62px;letter-spacing:4px;color:var(--white);text-transform:uppercase;line-height:1}
.hero-copy .btn-red{margin-top:40px;font-size:13px;padding:18px 30px}

/* stories */
.stories{padding:44px 0 0;height:880px}
.stories .wrap{display:flex;justify-content:space-between}
.top-stories{width:608px}
.latest-news{width:296px}
.feature{position:relative;margin-top:36px;height:376px}
.feature .photo{width:608px;height:376px;background:linear-gradient(135deg,#7b4a2a,#c4622f 45%,#8a3a1e 70%,#3d2515)}
.feature-card{position:absolute;left:0;bottom:40px;width:230px;background:var(--white);padding:14px 16px}
.tag{font-size:8px;color:var(--muted);text-transform:uppercase}
.card-title{font-family:"Roboto Slab",Georgia,serif;font-weight:700;font-size:13px;color:var(--ink);text-transform:uppercase;line-height:1.3}
.small-cards{display:flex;justify-content:space-between;margin-top:20px}
.small-card{width:192px}
.small-card .thumb{position:relative;height:160px}
.small-card .thumb .photo{height:160px;background:linear-gradient(150deg,#b04a22,#d98a3e 55%,#6b3a1e)}
.small-card .label{position:absolute;left:0;bottom:18px;width:120px;background:var(--white);padding:6px 8px;font-size:10px}
.small-card p{font-size:10px;line-height:1.5;margin:10px 0 12px}
.news-item{display:flex;gap:14px;margin-top:36px;height:100px}
.news-item .photo{width:100px;height:100px;flex:none;background:linear-gradient(135deg,#5a2f1a,#b24a22 60%,#d7883c)}
.news-item h4{font-size:11px}
.news-item p{font-size:10px;line-height:1.5;margin:6px 0}
.video{position:relative;height:292px;margin-top:36px}
.video .photo{height:230px;background:radial-gradient(circle at 50% 50%,#e3a458,#b0552a 55%,#5a3a22)}
.play{position:absolute;left:124px;top:91px}
.video h4{font-size:11px;margin-top:10px}
.video p{font-size:10px;line-height:1.4}

/* welcome */
.welcome{background:var(--band);height:340px;padding-top:56px}
.welcome-top{display:flex;align-items:flex-start}
.welcome-box{width:208px;height:120px;border:1px solid #cfcfcf;padding:22px 22px}
.welcome-box small{font-size:11px;text-transform:uppercase;color:var(--ink);letter-spacing:.5px}
.welcome-box .logo{font-size:38px;margin-top:8px}
.welcome-text{margin-left:52px;width:676px;font-size:12px;line-height:1.9;padding-top:6px}
.features{display:flex;margin-top:40px}
.feature-item{display:flex;align-items:center;gap:18px;width:312px}
.feature-item h5{font-family:"Roboto Slab",Georgia,serif;font-size:12px;color:var(--ink);text-transform:uppercase}
.feature-item p{font-size:10px}

/* recent posts */
.recent{height:940px;padding-top:108px}
.head-row{display:flex;justify-content:space-between;align-items:center}
.post{display:flex;align-items:center;border:1px solid var(--line);height:220px;margin-top:20px;padding:0 50px}
.head-row + .post{margin-top:32px}
.post .photo{width:150px;height:150px;border-radius:50%;flex:none;background:radial-gradient(circle,#f0b550,#d8772c 60%,#b04a22 80%,#d6a55a 82%,#c98a3c)}
.post-body{margin-left:70px;width:600px}
.post-body h3{font-family:"Roboto Slab",Georgia,serif;font-weight:700;font-size:15px;color:var(--ink);text-transform:uppercase;line-height:1.5}
.post-body p{font-size:12px;margin:10px 0 16px;width:440px}

/* galleries */
.galleries{background:var(--band);height:520px;padding-top:64px}
.grid{display:grid;grid-template-columns:repeat(4,228px);gap:12px 8px;margin-top:24px}
.grid .photo{height:182px}
.g1{background:linear-gradient(135deg,#6a2a18,#c4462a)}
.g2{background:linear-gradient(135deg,#3f2a1a,#b8632e)}
.g3{background:linear-gradient(135deg,#d7b98e,#9a6a3e)}
.g4{background:linear-gradient(135deg,#c7a07a,#7a4a2e)}
.g5{background:linear-gradient(135deg,#5a3a28,#c08a5a)}
.g6{background:linear-gradient(135deg,#efe6da,#d84a22)}
.g7{background:linear-gradient(135deg,#c66a3a,#7a3a22)}
.g8{background:linear-gradient(135deg,#e09a4a,#a8401e)}

/* partners */
.partners{height:320px;display:flex;justify-content:center;align-items:center;gap:70px}
.badge{width:180px;height:74px;background:#2a2a2a;border-radius:37px}
.badge.round{width:120px;height:74px;border-radius:50%;background:#6a3a22}
.badge.block{background:var(--red);border-radius:4px;width:200px}

/* footer */
.site-footer{background:var(--band);height:384px;padding-top:56px}
.footer-cols{display:flex;height:220px}
.footer-cols .logo{font-size:36px;margin-top:84px;width:268px}
.fcol h6{font-size:9px;color:var(--ink);text-transform:uppercase;font-weight:700;margin-bottom:12px}
.menu{width:160px}
.menu li{list-style:none;font-size:10px;line-height:1.9}
.contact{width:228px}
.contact li{list-style:none;font-size:10px;display:flex;gap:8px;align-items:flex-start;margin-bottom:8px;line-height:1.6}
.newsletter{width:280px}
.news-input{height:44px;background:var(--white);font-size:10px;color:var(--muted);padding:14px;border:1px solid var(--line)}
.newsletter .btn-red{float:right;margin-top:14px;font-size:11px;padding:12px 16px}
.footer-bottom{border-top:1px solid #d4d4d4;display:flex;justify-content:space-between;align-items:center;padding-top:30px}
.follow{display:flex;align-items:center;gap:8px;font-size:10px;font-weight:700;color:var(--red);text-transform:uppercase}
.dot{width:16px;height:16px;border-radius:50%;background:var(--red)}
.dot.b{background:#3d8ee8}.dot.c{background:#7d5cd1}
.copy{font-size:10px}
</style>
</head>
<body>

<header class="hero">
  <div class="photo hero-shade" role="img" aria-label="Overhead photo of a sliced pepperoni and olive pizza on a wooden table"></div>
  <div class="site-header">
    <div class="wrap">
      <div class="logo">Bim-Zee</div>
      <nav class="main-nav">
        <a class="active">Home</a><a>About us</a><a>Services</a><a>News</a><a>Blog</a><a>Contact us</a>
      </nav>
      <div class="search">Search</div>
    </div>
  </div>
  <div class="hero-copy">
    <h1>Tidy Hearth</h1>
    <a class="btn-red">Learn more ›</a>
  </div>
</header>

<section class="stories">
  <div class="wrap">
    <div class="top-stories">
      <h2 class="section-title">Top Stories</h2>
      <div class="feature">
        <div class="photo" role="img" aria-label="Close-up photo of a deep dish pizza with a slice lifted"></div>
        <div class="feature-card">
          <div class="tag">Category</div>
          <div class="card-title">Lorem Ipsum is simply dummy text of the printing</div>
        </div>
      </div>
      <div class="small-cards">
        <div class="small-card">
          <div class="thumb"><div class="photo" role="img" aria-label="Photo of pizza slices"></div><div class="label card-title">It is a long established</div></div>
          <p>Contrary to popular belief, Lorem Ipsum is not simply random text. It has roots.</p>
          <a class="btn-outline">Read more</a>
        </div>
        <div class="small-card">
          <div class="thumb"><div class="photo" role="img" aria-label="Photo of a pizza on a board"></div><div class="label card-title">There are many variations</div></div>
          <p>There are many variations of passages of Lorem Ipsum available, but the.</p>
          <a class="btn-outline">Read more</a>
        </div>
        <div class="small-card">
          <div class="thumb"><div class="photo" role="img" aria-label="Photo of a pepperoni pizza"></div><div class="label card-title">It is a long established</div></div>
          <p>It is a long established fact that a reader will be distracted by the readable content.</p>
          <a class="btn-outline">Read more</a>
        </div>
      </div>
    </div>

    <div class="latest-news">
      <h2 class="section-title">Latest News</h2>
      <div class="news-item">
        <div class="photo" role="img" aria-label="Thumbnail photo of a pizza"></div>
        <div><h4 class="card-title">There are many variations</h4><p>On the other hand, we denounce with righteous.</p><a class="btn-outline">Read more</a></div>
      </div>
      <div class="news-item">
        <div class="photo" role="img" aria-label="Thumbnail photo of a pizza slice"></div>
        <div><h4 class="card-title">At vero eos et accusamus</h4><p>On the other hand, we denounce with righteous.</p><a class="btn-outline">Read more</a></div>
      </div>
      <div class="news-item">
        <div class="photo" role="img" aria-label="Thumbnail photo of a baked pizza"></div>
        <div><h4 class="card-title">But I must explain to you</h4><p>On the other hand, we denounce with righteous.</p><a class="btn-outline">Read more</a></div>
      </div>
      <div class="video">
        <div class="photo" role="img" aria-label="Video still of a whole pizza seen from above"></div>
        <svg class="play" width="48" height="48" viewBox="0 0 48 48" aria-hidden="true"><circle cx="24" cy="24" r="24" fill="#fff"/><path d="M19 14l15 10-15 10z" fill="#222"/></svg>
        <h4 class="card-title">It is a long established</h4>
        <p>On the other hand, we denounce.</p>
      </div>
    </div>
  </div>
</section>

<section class="welcome">
  <div class="wrap">
    <div class="welcome-top">
      <div class="welcome-box"><small>Welcome to</small><div class="logo">Bim-Zee</div></div>
      <p class="welcome-text">There are many variations of passages of Lorem Ipsum available, but the majority have suffered alteration in some form, by injected humour, or randomised words which don't look even slightly believable. If you are going to use a passage.</p>
    </div>
    <div class="features">
      <div class="feature-item">
        <svg width="44" height="44" viewBox="0 0 44 44" aria-hidden="true"><circle cx="22" cy="22" r="22" fill="#e0102a"/><path d="M13 22l18-8-6 18-3-7z" fill="#fff"/></svg>
        <div><h5>Our Mission</h5><p>There are many variations</p></div>
      </div>
      <div class="feature-item">
        <svg width="44" height="44" viewBox="0 0 44 44" aria-hidden="true"><circle cx="22" cy="22" r="22" fill="#e0102a"/><circle cx="19" cy="20" r="6" fill="none" stroke="#fff" stroke-width="3"/><circle cx="28" cy="27" r="3.5" fill="none" stroke="#fff" stroke-width="2.5"/></svg>
        <div><h5>Customizable</h5><p>There are many variations</p></div>
      </div>
      <div class="feature-item">
        <svg width="44" height="44" viewBox="0 0 44 44" aria-hidden="true"><circle cx="22" cy="22" r="22" fill="#e0102a"/><path d="M13 25v-3a9 9 0 0118 0v3" fill="none" stroke="#fff" stroke-width="2.5"/><rect x="12" y="24" width="5" height="7" rx="2" fill="#fff"/><rect x="27" y="24" width="5" height="7" rx="2" fill="#fff"/></svg>
        <div><h5>Support</h5><p>There are many variations</p></div>
      </div>
    </div>
  </div>
</section>

<section class="recent">
  <div class="wrap">
    <div class="head-row"><h2 class="section-title">Recent Posts</h2><a class="btn-red">View all</a></div>
    <article class="post">
      <div class="photo" role="img" aria-label="Photo of a round pepperoni pizza"></div>
      <div class="post-body"><h3>Lorem Ipsum is simply dummy text of the printing and typesetting industry</h3><p>There are many variations of passages of Lorem Ipsum available, but the majority have suffered alteration in some form.</p><a class="btn-outline">Read more</a></div>
    </article>
    <article class="post">
      <div class="photo" role="img" aria-label="Photo of a cheese pizza"></div>
      <div class="post-body"><h3>There are many variations of passages of Lorem Ipsum available, but the majority have suffered</h3><p>There are many variations of passages of Lorem Ipsum available, but the majority have suffered alteration in some form.</p><a class="btn-outline">Read more</a></div>
    </article>
    <article class="post">
      <div class="photo" role="img" aria-label="Photo of a heart-shaped pizza"></div>
      <div class="post-body"><h3>But I must explain to you how all this mistaken idea of denouncing pleasure</h3><p>There are many variations of passages of Lorem Ipsum available, but the majority have suffered alteration in some form.</p><a class="btn-outline">Read more</a></div>
    </article>
  </div>
</section>

<section class="galleries">
  <div class="wrap">
    <div class="head-row"><h2 class="section-title">Latest Galleries</h2><a class="btn-red">View all</a></div>
    <div class="grid">
      <div class="photo g1" role="img" aria-label="Gallery photo of a pizza on a table"></div>
      <div class="photo g2" role="img" aria-label="Gallery photo of pizza slices"></div>
      <div class="photo g3" role="img" aria-label="Gallery photo of a chef preparing dough"></div>
      <div class="photo g4" role="img" aria-label="Gallery photo of guests sharing pizza"></div>
      <div class="photo g5" role="img" aria-label="Gallery photo of a person eating pizza"></div>
      <div class="photo g6" role="img" aria-label="Gallery photo of sauce being spread on dough"></div>
      <div class="photo g7" role="img" aria-label="Gallery photo of a sliced pizza"></div>
      <div class="photo g8" role="img" aria-label="Gallery photo of a cheese pizza"></div>
    </div>
  </div>
</section>

<section class="partners" aria-label="Partner brands">
  <div class="badge"></div>
  <div class="badge round"></div>
  <div class="badge block"></div>
  <div class="badge"></div>
</section>

<footer class="site-footer">
  <div class="wrap">
    <div class="footer-cols">
      <div class="logo">Bim-Zee</div>
      <div class="fcol menu"><h6>Menu</h6><ul><li>Home</li><li>About us</li><li>Services</li><li>News</li><li>Blog</li><li>Contact us</li></ul></div>
      <div class="fcol contact"><h6>Contact us</h6>
        <ul>
          <li><svg width="10" height="12" viewBox="0 0 10 12" aria-hidden="true"><path d="M5 0a4 4 0 014 4c0 3-4 8-4 8S1 7 1 4a4 4 0 014-4z" fill="#e0102a"/></svg><span>48 Larkspur Lane<br>Fenwold</span></li>
          <li><svg width="10" height="12" viewBox="0 0 10 12" aria-hidden="true"><path d="M2 0h3l1 3-2 1c1 2 2 3 3 4l1-2 3 1v3c-6 0-9-4-9-10z" fill="#e0102a"/></svg><span>555-014-2280</span></li>
          <li><svg width="10" height="12" viewBox="0 0 10 12" aria-hidden="true"><rect x="0" y="3" width="10" height="7" fill="#e0102a"/></svg><span>hello@bimzee.test</span></li>
        </ul>
      </div>
      <div class="fcol newsletter"><h6>Newsletter Subscribe</h6><div class="news-input">E-mail</div><a class="btn-red">Submit</a></div>
    </div>
    <div class="footer-bottom">
      <div class="follow">Follow us <span class="dot"></span><span class="dot b"></span><span class="dot c"></span></div>
      <div class="copy">Copyright © 2019 All Rights Reserved</div>
    </div>
  </div>
</footer>

</body>
</html>
```